EPS Recycling End Market Infographic

We need a two-page visual presentation of new end-market applications for recycled expanded polystyrene (EPS) collected for recycling. This focuses on expanded polystyrene (foam) transport packaging used for international distribution of goods, including pharmaceuticals and food, electronics, appliances and other products that need superior packaging protection.

The bulletin will have examples of 5 major industry categories that benefit from recycled EPS feedstock for reverse engineering to meet current market demand. It will also showcase names of companies that use recycled content EPS in their product manufacturing to legitimize end market adoption. The capability to use recycled EPS in new EPS packaging should be highlighted. We would like this bulletin to demonstrate the widespread application of recycled EPS in different industries and establish credibility that it is being used in a variety of interesting recycled-content products. We welcome creative and interesting font treatments and new trends in graphic design.

Target Market(s)

International Government Agencies, Packaging Engineers, Big Box Retailers, & Environmental Professionals

Industry/Entity Type

Plastic Manufacturers

Font styles to use
Sans Serif

Requirements
Must have
• Visual focus points, multiple examples of products and manufacturers as evidence to the information content
Should not have
• Insufficient white space or outdated design elements (like two-tone gradients).

```html
<!DOCTYPE html>
<html lang="en">
<head>
<meta charset="utf-8">
<title>Recycled EPS End Market Bulletin</title>
<link href="https://fonts.googleapis.com/css2?family=Plus+Jakarta+Sans:wght@400;500;600;700&display=swap" rel="stylesheet">
<style>
:root{
  --stage:#8f8f8f;
  --paper:#e9eef4;
  --steel:#5b8ba5;
  --olive:#9aa21e;
  --orange:#f5a623;
  --brown:#5a2a1a;
  --gold:#b8870f;
  --slate:#2f4254;
  --heading:#6b2e1c;
  --ink:#1f1f1f;
  --white:#ffffff;
}
*{box-sizing:border-box;margin:0;padding:0}
html,body{width:1200px;height:2848px;overflow:hidden}
body{background:var(--stage);font-family:"Plus Jakarta Sans",Arial,sans-serif;position:relative}
.page{position:absolute;left:90px;width:1020px;height:1320px;background:var(--paper);overflow:hidden}
.page-one{top:75px}
.page-two{top:1452px}
.abs{position:absolute}

/* header */
.header-band{position:absolute;left:0;top:0;width:760px;height:139px}
.header-title{position:absolute;left:60px;top:22px;color:var(--white);font-weight:700;font-size:37px;line-height:48px;letter-spacing:-0.5px}
.brand{position:absolute;left:778px;top:18px;display:flex;align-items:center;gap:12px}
.brand-dot{width:96px;height:96px;border-radius:50%;background:var(--gold)}
.brand-name{color:var(--gold);font-size:19px;line-height:21px;font-weight:500}

/* headings */
.section-title{position:absolute;left:0;width:100%;text-align:center;color:var(--heading);font-weight:700;font-size:30px;letter-spacing:-0.5px}
.section-rule{position:absolute;left:463px;width:94px;height:3px;background:var(--gold)}

/* stat */
.stat{position:absolute;left:548px;top:404px;width:400px;text-align:center}
.stat-number{color:#e8a21f;font-weight:700;font-size:42px}
.stat-unit{color:var(--steel);font-size:28px;font-weight:500}
.stat-caption{font-size:15.5px;line-height:23px;font-weight:600;color:#333;margin-top:2px}
.cooler-caption{position:absolute;left:560px;top:612px;width:380px;text-align:center;font-size:19px;font-weight:600;color:var(--ink)}

/* applications */
.apps{position:absolute;left:0;top:816px;width:1020px;height:394px;display:flex}
.app{flex:1;border-radius:102px 102px 0 0;display:flex;flex-direction:column;align-items:center;padding:17px 14px 0;text-align:center;color:var(--white)}
.app-photo{width:171px;height:171px;border-radius:50%;flex:none}
.app-title{font-size:17.5px;font-weight:600;line-height:22px;height:48px;display:flex;align-items:center;margin-top:12px}
.app-text{font-size:11.2px;line-height:17px;margin-top:10px;letter-spacing:-0.3px}
.app-olive{background:var(--olive)}
.app-orange{background:var(--orange)}
.app-steel{background:var(--steel)}
.app-brown{background:var(--brown)}
.app-gold{background:var(--gold)}
.photo-build{background:#d9a33a}
.photo-textile{background:#7a5e4e}
.photo-deck{background:#36454e}
.photo-paint{background:#e39a55}
.photo-print{background:#d9505e}

/* did you know */
.fact-band{position:absolute;left:0;top:1210px;width:1020px;height:110px}
.fact-label{position:absolute;left:40px;top:1210px;width:320px;height:110px;display:flex;align-items:center;justify-content:center;color:var(--white);font-size:29px;font-weight:600}
.fact-text{position:absolute;left:430px;top:1228px;width:560px;text-align:center;color:var(--heading);font-size:22px;line-height:36px;font-weight:600}
.fact-text .accent{color:var(--gold);font-weight:700}

/* users */
.user{position:absolute;top:300px;width:166px;height:196px;background:var(--white)}
.user-tag{position:absolute;top:-13px;left:22px;width:122px;height:26px;color:var(--white);font-size:14px;font-weight:600;display:flex;align-items:center;justify-content:center;white-space:nowrap}
.user-photo{position:absolute;left:33px;top:42px;width:100px;height:88px;border-radius:8px}
.user-caption{position:absolute;left:0;top:140px;width:100%;height:44px;display:flex;align-items:center;justify-content:center;text-align:center;color:var(--heading);font-size:17px;line-height:21px;font-weight:600}

/* product rainbow */
.band-label{position:absolute;color:var(--white);font-size:19px;line-height:23px;font-weight:600;text-align:right;letter-spacing:-0.3px}

/* footer */
.contact{position:absolute;left:622px;color:var(--white)}
.contact-label{font-size:14.5px;font-weight:400}
.contact-value{font-size:15px;font-weight:600;margin-top:2px;white-space:nowrap}
</style>
</head>
<body>

<!-- PAGE ONE -->
<section class="page page-one">
  <svg class="header-band" viewBox="0 0 760 139"><polygon points="0,0 757,0 707,70 757,139 0,139" fill="var(--steel)"/></svg>
  <h1 class="header-title">Recycled EPS: Powering the Next<br>Generation of Sustainable Packaging</h1>
  <div class="brand"><span class="brand-dot"></span><span class="brand-name">Foam Loop<br>Council</span></div>

  <h2 class="section-title" style="top:174px">Recycled EPS: Powering New Possibilities Across Industries</h2>
  <div class="section-rule" style="top:222px"></div>

  <svg class="abs cycle" style="left:0;top:0" width="560" height="760" viewBox="0 0 560 760" aria-label="Recycling loop: collection, recycling, new product manufacturing">
    <defs>
      <path id="arcCollect" d="M92 472 A171 171 0 0 1 239.2 302.7"/>
      <path id="arcRecycle" d="M321.5 311.3 A171 171 0 0 1 423.7 530.5"/>
      <path id="arcMake" d="M361.1 612.1 A171 171 0 0 1 114.9 557.5"/>
    </defs>
    <use href="#arcCollect" fill="none" stroke="var(--olive)" stroke-width="56"/>
    <polygon points="232.3,253.2 246.2,352.2 308.5,293" fill="var(--olive)"/>
    <use href="#arcRecycle" fill="none" stroke="var(--steel)" stroke-width="56"/>
    <polygon points="470.7,547.6 376.7,513.4 399.8,596.3" fill="var(--steel)"/>
    <use href="#arcMake" fill="none" stroke="var(--gold)" stroke-width="56"/>
    <polygon points="71.6,582.5 158.2,532.5 79.9,496.9" fill="var(--gold)"/>
    <g fill="var(--white)" font-weight="600" font-family="Plus Jakarta Sans, Arial, sans-serif">
      <text dy="7" font-size="21"><textPath href="#arcCollect" startOffset="50%" text-anchor="middle">EPS Collection</textPath></text>
      <text dy="7" font-size="21"><textPath href="#arcRecycle" startOffset="50%" text-anchor="middle">Recycling</textPath></text>
      <text dy="6" font-size="18"><textPath href="#arcMake" startOffset="50%" text-anchor="middle">New Product Manufacturing</textPath></text>
    </g>
    <circle cx="263" cy="472" r="82" fill="var(--white)"/>
    <circle cx="263" cy="472" r="73" fill="none" stroke="var(--heading)" stroke-width="2"/>
    <circle cx="263" cy="472" r="64" fill="var(--gold)"/>
    <text x="263" y="466" text-anchor="middle" fill="var(--white)" font-size="20" font-weight="600" font-family="Plus Jakarta Sans, Arial, sans-serif">Foam</text>
    <text x="263" y="490" text-anchor="middle" fill="var(--white)" font-size="20" font-weight="600" font-family="Plus Jakarta Sans, Arial, sans-serif">Loop</text>
  </svg>

  <svg class="abs" style="left:548px;top:281px" width="400" height="310" viewBox="0 0 400 310" role="img" aria-label="Photo of a white recycled-content EPS foam cooler">
    <defs><linearGradient id="coolerTone" x1="0" y1="0" x2="0" y2="1"><stop offset="0" stop-color="#f7f7f5"/><stop offset="1" stop-color="#dcdedc"/></linearGradient></defs>
    <path d="M8 30 Q200 0 392 30 L392 60 L355 288 Q200 305 45 288 L8 60 Z" fill="url(#coolerTone)"/>
  </svg>
  <div class="stat">
    <div><span class="stat-number">30,800</span> <span class="stat-unit">Tons</span></div>
    <div class="stat-caption">OF Expanded Polystyrene (EPS)<br>Was Recycled in 2022</div>
  </div>
  <div class="cooler-caption">Recycled Content EPS Cooler</div>
  <svg class="abs" style="left:880px;top:480px" width="50" height="160" viewBox="0 0 50 160">
    <path d="M14 144 Q50 100 24 14" fill="none" stroke="var(--olive)" stroke-width="2" stroke-dasharray="4 4"/>
    <path d="M16 22 L24 12 L30 24" fill="none" stroke="var(--olive)" stroke-width="2"/>
  </svg>

  <h2 class="section-title" style="top:727px">5 Key Industry Applications</h2>
  <div class="section-rule" style="top:774px"></div>

  <div class="apps">
    <article class="app app-olive">
      <div class="app-photo photo-build" role="img" aria-label="Photo of a hard hat beside a small wooden house model"></div>
      <h3 class="app-title">Construction &amp;<br>Architectural</h3>
      <p class="app-text">Walls, insulation, and geofoam are all products that can utilize recycled EPS as part of the design. Ground or shredded EPS be mixed in with concrete or asphalt to improve quality</p>
    </article>
    <article class="app app-orange">
      <div class="app-photo photo-textile" role="img" aria-label="Photo of fabric swatches in earthy tones"></div>
      <h3 class="app-title">Textile &amp;<br>Fiber</h3>
      <p class="app-text">Specialized techniques produce fine fibers of EPS to be used in non-woven mats and in nanofibers to help absorb oil spills.</p>
    </article>
    <article class="app app-steel">
      <div class="app-photo photo-deck" role="img" aria-label="Photo of dark composite deck boards with green leaves"></div>
      <h3 class="app-title">Wood Composites &amp;<br>Blends</h3>
      <p class="app-text">Novel applications using EPS can avoid traditional glue use in wood composites by combining EPS with waste wood fibers.</p>
    </article>
    <article class="app app-brown">
      <div class="app-photo photo-paint" role="img" aria-label="Photo of open paint cans with a brush"></div>
      <h3 class="app-title">Paints, Coatings,<br>Adhesives</h3>
      <p class="app-text">Water resistant paints are needed for architectural and roadway applications. EPS can be recycled into a resin and mixed into paint to enhance water resistance.</p>
    </article>
    <article class="app app-gold">
      <div class="app-photo photo-print" role="img" aria-label="Photo of a 3D printer nozzle printing a red lattice object"></div>
      <h3 class="app-title">Additives</h3>
      <p class="app-text">Modern approaches to plastics manufacturing can use recycle EPS to create material for 3D printing.</p>
    </article>
  </div>

  <svg class="fact-band" viewBox="0 0 1020 110"><polygon points="0,0 407,0 372,55 407,110 0,110" fill="var(--slate)"/></svg>
  <div class="fact-label">Did You Know?</div>
  <p class="fact-text">New EPS packaging can now be made with up to<br><span class="accent">50%</span> recycled content.</p>
</section>

<!-- PAGE TWO -->
<section class="page page-two">
  <svg class="header-band" viewBox="0 0 760 139"><polygon points="0,0 757,0 707,70 757,139 0,139" fill="var(--steel)"/></svg>
  <h1 class="header-title">Recycled EPS: Powering the Next<br>Generation of Sustainable Packaging</h1>
  <div class="brand"><span class="brand-dot"></span><span class="brand-name">Foam Loop<br>Council</span></div>

  <h2 class="section-title" style="top:191px">Who’s Using Recycled EPS?</h2>
  <div class="section-rule" style="top:239px"></div>

  <div class="user" style="left:62px"><span class="user-tag" style="background:var(--gold)">Kestrel Forms</span><div class="user-photo" role="img" aria-label="White moulded automotive foam part" style="background:#dedede"></div><p class="user-caption">Automotive<br>components</p></div>
  <div class="user" style="left:244px"><span class="user-tag" style="background:var(--brown)">Birchline 42</span><div class="user-photo" role="img" aria-label="Blue patio bench" style="background:#6f94ab"></div><p class="user-caption">Patio Bench</p></div>
  <div class="user" style="left:427px"><span class="user-tag" style="background:var(--steel)">Greenway Goods</span><div class="user-photo" role="img" aria-label="Black disposable spoon" style="background:#3a3a3a"></div><p class="user-caption">Spoon</p></div>
  <div class="user" style="left:608px"><span class="user-tag" style="background:var(--orange)">Aldova</span><div class="user-photo" role="img" aria-label="Brown clothing hanger" style="background:#a0714f"></div><p class="user-caption">Clothing<br>hangers</p></div>
  <div class="user" style="left:790px"><span class="user-tag" style="background:var(--olive)">Tidal Foamworks</span><div class="user-photo" role="img" aria-label="White surfboard blank" style="background:#e4ded6"></div><p class="user-caption">Surfboard<br>blanks</p></div>

  <h2 class="section-title" style="top:574px">Products That Use EPS Recycled</h2>
  <div class="section-rule" style="top:624px"></div>

  <svg class="abs" style="left:0;top:0" width="1020" height="1320" viewBox="0 0 1020 1320" aria-label="End uses of recycled EPS">
    <g fill="none" stroke-width="76">
      <path d="M955 714 H440 A337 475 0 0 0 103 1189 A250 200 0 0 0 353 1389" stroke="var(--olive)"/>
      <path d="M893 800 H460 A282 389 0 0 0 178 1189 A175 150 0 0 0 353 1339" stroke="var(--orange)"/>
      <path d="M827 890 H470 A218 299 0 0 0 252 1189 A101 110 0 0 0 353 1299" stroke="var(--steel)"/>
      <path d="M758 977 H480 A160 212 0 0 0 320 1189" stroke="var(--brown)"/>
      <path d="M683 1064 H470 A110 125 0 0 0 360 1189" stroke="var(--gold)"/>
    </g>
    <g fill="var(--white)">
      <circle cx="955" cy="714" r="38" fill="var(--olive)"/>
      <circle cx="893" cy="800" r="38" fill="var(--orange)"/>
      <circle cx="827" cy="890" r="38" fill="var(--steel)"/>
      <circle cx="758" cy="977" r="38" fill="var(--brown)"/>
      <circle cx="683" cy="1064" r="38" fill="var(--gold)"/>
      <circle cx="882" cy="714" r="33"/>
      <circle cx="818" cy="800" r="33"/>
      <circle cx="754" cy="890" r="33"/>
      <circle cx="686" cy="977" r="33"/>
      <circle cx="613" cy="1064" r="33"/>
    </g>
    <g fill="none" stroke-width="3" stroke-linecap="round">
      <path d="M866 722 H898 M866 712 H898 M870 702 v-6 M882 702 v-6 M894 702 v-6" stroke="var(--olive)"/>
      <path d="M806 790 H830 L822 800 H814 Z M818 802 V808 M804 814 H832" stroke="var(--orange)"/>
      <path d="M738 900 H770 M738 892 H770 M742 884 v-8 M754 884 v-8 M766 884 v-8" stroke="var(--steel)"/>
      <path d="M674 965 V989 M686 965 V989 M698 965 V989 M668 971 H704 M668 983 H704" stroke="var(--brown)"/>
      <path d="M601 1052 H625 V1076 H601 Z M601 1060 H625 M601 1068 H625" stroke="var(--gold)"/>
    </g>
    <circle cx="351" cy="1189" r="72" fill="var(--olive)"/>
    <circle cx="351" cy="1189" r="64" fill="var(--white)"/>
    <circle cx="351" cy="1189" r="56" fill="var(--gold)"/>
    <text x="351" y="1184" text-anchor="middle" fill="var(--white)" font-size="18" font-weight="600" font-family="Plus Jakarta Sans, Arial, sans-serif">Foam</text>
    <text x="351" y="1206" text-anchor="middle" fill="var(--white)" font-size="18" font-weight="600" font-family="Plus Jakarta Sans, Arial, sans-serif">Loop</text>

    <polygon points="484,1180 1020,1180 1020,1320 520,1320" fill="var(--steel)"/>
    <circle cx="586" cy="1220" r="20" fill="var(--olive)"/>
    <path d="M586 1208 a8 8 0 0 1 8 8 c0 6 -8 14 -8 14 s-8 -8 -8 -14 a8 8 0 0 1 8 -8 z" fill="var(--white)"/>
    <circle cx="586" cy="1216" r="3" fill="var(--olive)"/>
    <circle cx="586" cy="1278" r="20" fill="var(--olive)"/>
    <path d="M579 1268 l5 5 -3 4 c2 4 5 7 9 9 l4 -3 5 5 -3 4 c-9 0 -21 -12 -21 -21 z" fill="var(--white)"/>
  </svg>

  <p class="band-label" style="right:200px;top:690px">Lightweight Concrete Insulation Panels/Blocks<br>Geofoam &amp; Soil Improvement</p>
  <p class="band-label" style="right:264px;top:776px">3D Printing Filaments Direct Ink Writing<br>Injection Molding &amp; Extrusion</p>
  <p class="band-label" style="right:328px;top:866px">Protective &amp; Hydrophobic Coatings<br>Adhesives &amp; Sealants</p>
  <p class="band-label" style="right:396px;top:953px">Non-Woven Fabrics Fiber<br>Absorbents Filters</p>
  <p class="band-label" style="right:468px;top:1040px">Composite Binders<br>Glue</p>

  <div class="contact" style="top:1196px"><div class="contact-label">Address</div><div class="contact-value">4470 Harbor Point Rd, Ste. 310 Lakewood, OH 44107</div></div>
  <div class="contact" style="top:1254px"><div class="contact-label">Phone Number</div><div class="contact-value">800-555-0142</div></div>
</section>

</body>
</html>
```